Can you make a cool and versatile Tarn Meridian Powerpoint template?
See www.tarnmeridian-example.co.uk and http://www.examplenet.invalid/company/tarn-meridian-ltd/ (on the right) to see how the logos are currently used - with interchangeably white and black backgrounds.
Target Market(s)
Marketing managers, product managers in HR technology, HR consultants
Industry/Entity Type
It Company
Font styles to use
Sans Serif
Requirements
Must have
- Master slide design, fonts, color theme, etc. Ideally two variations - one with white background (using colorful logo), one with a darker background (using black/white logo).

```html
<!DOCTYPE html>
<html lang="en">
<head>
<meta charset="utf-8">
<title>Tarn Meridian – Template with Dark Background_V1</title>
<link rel="stylesheet" href="https://fonts.googleapis.com/css2?family=Arimo:wght@400&family=Carlito&display=swap">
<style>
  :root {
    --sheet-bg: #d9d9d9;
    --heading-ink: #111111;
    --slide-bg: #222222;
    --slide-shape: #363636;
    --slide-text: #f2f2f2;
    --slide-muted: #5a5a5a;
    --mark: #ffffff;
  }
  * { box-sizing: border-box; margin: 0; padding: 0; }
  html, body { width: 1200px; height: 900px; overflow: hidden; }
  body {
    position: relative;
    background: var(--sheet-bg);
    font-family: "Arimo", Arial, sans-serif;
  }
  .sheet-title {
    position: absolute;
    left: 0; top: 72px; width: 1142px;
    text-align: center;
    font-family: "Carlito", Calibri, sans-serif;
    font-size: 28px; font-weight: 400;
    color: var(--heading-ink);
  }
  .slide {
    position: absolute;
    width: 346px; height: 259px;
    background: var(--slide-bg);
    overflow: hidden;
    color: var(--slide-text);
  }
  .slide--cover   { left: 38px;  top: 168px; }
  .slide--divider { left: 414px; top: 168px; }
  .slide--content { left: 784px; top: 168px; }
  .slide--right   { left: 38px;  top: 457px; }
  .slide--closing { left: 414px; top: 457px; }

  .backdrop-circle {
    position: absolute;
    border-radius: 50%;
    background: var(--slide-shape);
  }
  .brand {
    position: absolute;
    display: flex; align-items: center; gap: 7px;
    color: var(--slide-text);
    font-weight: 400;
    white-space: nowrap;
  }
  .brand-dot {
    border-radius: 50%;
    background: var(--mark);
    flex: none;
  }
  .brand--large { font-size: 17px; }
  .brand--large .brand-dot { width: 12px; height: 12px; }
  .brand--medium { font-size: 12px; gap: 5px; }
  .brand--medium .brand-dot { width: 9px; height: 9px; }
  .brand--small { font-size: 6px; gap: 3px; right: 4px; bottom: 3px; }
  .brand--small .brand-dot { width: 5px; height: 5px; }
  .corner-dot {
    position: absolute; left: 6px; top: 4px;
    width: 14px; height: 14px; border-radius: 50%;
    background: var(--mark);
  }
  .slide-title {
    position: absolute;
    font-size: 12px; font-weight: 400;
    color: var(--slide-text);
  }
  .slide-date {
    position: absolute;
    font-size: 6px; color: var(--slide-muted);
  }
  .centered { left: 0; width: 100%; text-align: center; }
  .bullets { position: absolute; list-style: none; font-size: 8.5px; line-height: 12px; }
  .bullets li::before { display: inline-block; width: 8px; }
  .bullets .l1::before { content: "•"; }
  .bullets .l2 { padding-left: 16px; } .bullets .l2::before { content: "–"; }
  .bullets .l3 { padding-left: 32px; } .bullets .l3::before { content: "•"; font-size: 6px; }
  .bullets .l4 { padding-left: 50px; } .bullets .l4::before { content: "–"; }
  .bullets .l5 { padding-left: 68px; } .bullets .l5::before { content: "•"; font-size: 6px; }
  .bullets--compact { font-size: 7.5px; line-height: 11.3px; }
</style>
</head>
<body>
  <h1 class="sheet-title">Template with Dark Background_V1</h1>

  <section class="slide slide--cover">
    <div class="backdrop-circle" style="left:110px; top:-30px; width:170px; height:170px;"></div>
    <div class="brand brand--large" style="left:116px; top:46px;"><span class="brand-dot"></span>Tarn Meridian</div>
    <p class="slide-title centered" style="top:146px;">Presentation Template</p>
    <p class="slide-date centered" style="top:165px;">November 12, 2013</p>
  </section>

  <section class="slide slide--divider">
    <div class="backdrop-circle" style="left:70px; top:20px; width:100px; height:100px;"></div>
    <div class="brand brand--medium" style="left:206px; top:89px;"><span class="brand-dot"></span>Tarn Meridian</div>
    <p class="slide-title" style="left:14px; top:151px; font-size:13px;">Divider</p>
  </section>

  <section class="slide slide--content">
    <span class="corner-dot"></span>
    <p class="slide-title" style="left:21px; top:32px; font-size:13px;">Title and Bulleted Content</p>
    <ul class="bullets" style="left:21px; top:55px;">
      <li class="l1">Click to edit Master text styles</li>
      <li class="l2">Second level</li>
      <li class="l3">Third level</li>
      <li class="l4">Fourth level</li>
      <li class="l5">Fifth level</li>
    </ul>
    <div class="brand brand--small"><span class="brand-dot"></span>Tarn Meridian</div>
  </section>

  <section class="slide slide--right">
    <span class="corner-dot"></span>
    <p class="slide-title" style="left:185px; top:25px; width:155px; font-size:11px; line-height:13px;">Title and Bulleted Content on the Right</p>
    <ul class="bullets bullets--compact" style="left:185px; top:61px;">
      <li class="l1">Click to edit Master text styles</li>
      <li class="l2">Second level</li>
      <li class="l3">Third level</li>
      <li class="l4">Fourth level</li>
      <li class="l5">Fifth level</li>
    </ul>
    <div class="brand brand--small"><span class="brand-dot"></span>Tarn Meridian</div>
  </section>

  <section class="slide slide--closing">
    <div class="backdrop-circle" style="left:105px; top:-45px; width:170px; height:170px;"></div>
    <div class="brand brand--large" style="left:116px; top:46px; font-size:16px;"><span class="brand-dot"></span>Tarn Meridian</div>
    <p class="slide-title centered" style="top:146px;">Thank You</p>
    <p class="slide-date centered" style="top:165px;">November 12, 2013</p>
  </section>
</body>
</html>
```